Redesign Comparisson chart - make modern and effective

Use your imaginations to make a powerful distinction between KMV & other holistic modalities. There are 7 elements physical, mental, emotional, energetic, subconscious, superconscious and before and after testing.
We want it to be obvious that KMV is the only modality that works on all these elements simultaneously. We do not want to include any chakras as we want this information to be accepted by a wide range of people and belief systems.'

We want it to look simple but effective. Professional but powerful. We want KMV to stand out even of you eye just passed over i.
Updates

Hi everyone, thanks for your submissions so far. Basically what this image is meant to represent is a comparison chart between all the modalities There are 5 elements physical, mental, emotional, subconscious and superconscious. we want to reflect that KMV is the only modality that works on all these elements simultaneously. As we want the concept to be accepted and not considered woo woo, we want to steer away from chakras.

Target Market(s)

Professionals

Industry/Entity Type

Professional services

Font styles to use
Sans Serif
Other font styles liked:
• Poppins Monserratt

Colors
0094D4
00A9DD
6FCCEA
C7EBF8
E9F6FB

Requirements
Must have
• Clear/professional and clean look. Brand colours and logos. All typography and formats must be cohesive.
Nice to have
• More easy to read, different layout
Should not have
• Do not change the data just the way its presented. No chakras

```html
<!DOCTYPE html>
<html lang="en">
<head>
<meta charset="utf-8">
<title>KMV Comparison Chart</title>
<link href="https://fonts.googleapis.com/css2?family=Poppins:wght@300;400;600;700;800&display=swap" rel="stylesheet">
<style>
:root{
  --brand-deep:#0094D4;
  --brand:#00A9DD;
  --brand-row:#1AB2E2;
  --brand-line:#6FCCEA;
  --brand-pale:#C7EBF8;
  --brand-mist:#E9F6FB;
  --physical:#FF3D00;
  --mental:#1E88D8;
  --emotional:#8CC63F;
  --energetic:#FBA83C;
  --subconscious:#F5E93A;
  --superconscious:#7B2A8E;
  --testing:#C4228E;
  --ink:#222;
  --grey:#666;
}
*{box-sizing:border-box;margin:0;padding:0}
html,body{width:873px;height:1200px;overflow:hidden;background:#fff}
body{position:relative;font-family:'Poppins',sans-serif;color:var(--ink)}
.band{position:absolute;left:0;top:125px;width:873px;height:798px;background:var(--brand-pale)}
.headline{position:absolute;left:318px;width:512px;top:54px;text-align:center}
.headline h1{font-weight:800;font-size:17.5px;color:var(--mental);letter-spacing:-.2px}
.headline p{font-size:10.6px;line-height:13.2px;color:var(--grey);margin-top:2px}
.panel{position:absolute;left:90px;top:125px;width:749px;height:798px;background:var(--brand);border-radius:10px}
.brand-box{position:absolute;left:110px;top:89px;width:169px;height:71px;background:#fff;border:2px solid var(--brand-deep);border-radius:4px;display:flex;align-items:center;justify-content:center;z-index:2}
.brand-name{font-weight:800;font-size:34px;color:var(--brand-deep);letter-spacing:1px}
.heads{position:absolute;left:307px;top:135px;display:flex}
.heads span{width:73.5px;height:28px;display:flex;align-items:center;justify-content:center;text-align:center;font-size:8.2px;line-height:10px;color:#fff;border:1px solid var(--brand-line)}
.h-physical{background:var(--physical)}
.h-mental{background:#fff;color:var(--mental)!important}
.h-emotional{background:var(--emotional)}
.h-energetic{background:var(--energetic)}
.h-subconscious{background:var(--subconscious);color:var(--mental)!important}
.h-superconscious{background:var(--superconscious)}
.h-testing{background:var(--testing)}
.chart{position:absolute;left:90px;top:163px;width:749px}
.row{display:flex;position:relative}
.row .label{width:217px;padding-left:20px;display:flex;flex-direction:column;justify-content:center;font-weight:400;font-size:12px;line-height:17.5px;color:#fff;text-transform:uppercase}
.row.alt .label{background:var(--brand-row)}
.row .cell{width:73.5px;display:flex;align-items:center;justify-content:center;border-left:1px solid var(--brand-line);border-bottom:1px solid var(--brand-line)}
.row .cell:last-child{border-right:1px solid var(--brand-line)}
.star{width:23px;height:23px}
.star path{stroke:#fff;stroke-width:1.2}
.p{color:var(--physical)}.m{color:var(--mental)}.e{color:var(--emotional)}.n{color:var(--energetic)}.s{color:var(--subconscious)}.u{color:var(--superconscious)}.t{color:var(--testing)}
.row.hero{z-index:2}
.row.hero::before{content:"";position:absolute;left:-40px;right:-12px;top:0;bottom:0;background:#B4E4F5;border:1.5px solid var(--brand-deep);border-radius:3px;box-shadow:0 3px 5px rgba(0,0,0,.3)}
.row.hero .label,.row.hero .cell{position:relative;border-color:rgba(111,204,234,.5)}
.row.hero .label{padding-left:20px}
.hero-name{font-weight:800;font-size:14px;color:var(--brand-deep)}
.row.hero .star{width:30px;height:30px}
.row.hero .star path{stroke:none}
.legend{position:absolute;top:942px;left:80px;width:760px;display:grid;grid-template-columns:363px 365px;column-gap:32px}
.legend .col{display:flex;flex-direction:column;gap:12px}
.legend p{font-size:11.6px;line-height:14.4px;text-align:justify;padding-left:11px;text-indent:-11px}
.tag{display:inline-block;text-indent:0;color:#fff;font-weight:700;font-size:12.5px;line-height:14.5px;padding:0 3px 0 11px;margin-right:3px;letter-spacing:.2px}
.tag.physical{background:var(--physical)}
.tag.mental{background:var(--mental)}
.tag.emotional{background:var(--emotional)}
.tag.energetic{background:var(--energetic)}
.tag.subconscious{background:var(--subconscious)}
.tag.superconscious{background:var(--superconscious)}
.tag.testing{background:var(--testing)}
</style>
</head>
<body>
<svg width="0" height="0" style="position:absolute">
  <symbol id="spark" viewBox="0 0 24 24"><path fill="currentColor" d="M12 1C13 8.5 15.5 11 23 12C15.5 13 13 15.5 12 23C11 15.5 8.5 13 1 12C8.5 11 11 8.5 12 1Z"/></symbol>
</svg>

<div class="band"></div>

<header class="headline">
  <h1>Choose KMV For Fast, Immediate and Powerful Results.</h1>
  <p>I must experience healing on all levels I am not just a body I want to learn how to heal myself so i’m not dependent on others. I want to release all my emotional and mental blocks so I can be the best version of myself.</p>
</header>

<div class="panel"></div>

<div class="brand-box"><span class="brand-name">KMV</span></div>

<div class="heads">
  <span class="h-physical">PHYSICAL</span>
  <span class="h-mental">MENTAL</span>
  <span class="h-emotional">EMOTIONAL</span>
  <span class="h-energetic">ENERGETIC</span>
  <span class="h-subconscious">SUB<br>CONSCIOUS</span>
  <span class="h-superconscious">SUPER<br>CONSCIOUS</span>
  <span class="h-testing">BEFORE &amp;<br>AFTER TESTING</span>
</div>

<div class="chart">
  <div class="row" style="height:107px"><div class="label">Massage<br>Yoga<br>Natropathy<br>Ayurvedic Medicine<br>Western Medicine</div>
    <div class="cell"><svg class="star p"><use href="#spark"/></svg></div><div class="cell"></div><div class="cell"></div><div class="cell"></div><div class="cell"></div><div class="cell"></div><div class="cell"></div></div>
  <div class="row alt" style="height:34px"><div class="label">Psychic Intuitive</div>
    <div class="cell"><svg class="star p"><use href="#spark"/></svg></div><div class="cell"><svg class="star m"><use href="#spark"/></svg></div><div class="cell"></div><div class="cell"></div><div class="cell"></div><div class="cell"></div><div class="cell"></div></div>
  <div class="row" style="height:36px"><div class="label">Family Constellation</div>
    <div class="cell"><svg class="star p"><use href="#spark"/></svg></div><div class="cell"><svg class="star m"><use href="#spark"/></svg></div><div class="cell"></div><div class="cell"><svg class="star n"><use href="#spark"/></svg></div><div class="cell"></div><div class="cell"></div><div class="cell"></div></div>
  <div class="row alt" style="height:34px"><div class="label">Acupuncture</div>
    <div class="cell"><svg class="star p"><use href="#spark"/></svg></div><div class="cell"></div><div class="cell"></div><div class="cell"><svg class="star n"><use href="#spark"/></svg></div><div class="cell"></div><div class="cell"></div><div class="cell"></div></div>
  <div class="row" style="height:37px"><div class="label">Nutritional Healing</div>
    <div class="cell"><svg class="star p"><use href="#spark"/></svg></div><div class="cell"></div><div class="cell"></div><div class="cell"></div><div class="cell"></div><div class="cell"></div><div class="cell"><svg class="star t"><use href="#spark"/></svg></div></div>
  <div class="row alt" style="height:34px"><div class="label">Chinese Medicine</div>
    <div class="cell"><svg class="star p"><use href="#spark"/></svg></div><div class="cell"></div><div class="cell"></div><div class="cell"><svg class="star n"><use href="#spark"/></svg></div><div class="cell"></div><div class="cell"></div><div class="cell"><svg class="star t"><use href="#spark"/></svg></div></div>
  <div class="row" style="height:48px"><div class="label">Kinesiology<br>Bowen Therapy</div>
    <div class="cell"><svg class="star p"><use href="#spark"/></svg></div><div class="cell"></div><div class="cell"></div><div class="cell"></div><div class="cell"><svg class="star s"><use href="#spark"/></svg></div><div class="cell"></div><div class="cell"><svg class="star t"><use href="#spark"/></svg></div></div>
  <div class="row hero" style="height:43px"><div class="label"><span class="hero-name">KMV</span></div>
    <div class="cell"><svg class="star p"><use href="#spark"/></svg></div><div class="cell"><svg class="star m"><use href="#spark"/></svg></div><div class="cell"><svg class="star e"><use href="#spark"/></svg></div><div class="cell"><svg class="star n"><use href="#spark"/></svg></div><div class="cell"><svg class="star s"><use href="#spark"/></svg></div><div class="cell"><svg class="star u"><use href="#spark"/></svg></div><div class="cell"><svg class="star t"><use href="#spark"/></svg></div></div>
  <div class="row" style="height:34px"><div class="label">EFT</div>
    <div class="cell"><svg class="star p"><use href="#spark"/></svg></div><div class="cell"><svg class="star m"><use href="#spark"/></svg></div><div class="cell"></div><div class="cell"></div><div class="cell"><svg class="star s"><use href="#spark"/></svg></div><div class="cell"></div><div class="cell"><svg class="star t"><use href="#spark"/></svg></div></div>
  <div class="row alt" style="height:33px"><div class="label">Chiropratic</div>
    <div class="cell"><svg class="star p"><use href="#spark"/></svg></div><div class="cell"></div><div class="cell"></div><div class="cell"><svg class="star n"><use href="#spark"/></svg></div><div class="cell"><svg class="star s"><use href="#spark"/></svg></div><div class="cell"></div><div class="cell"><svg class="star t"><use href="#spark"/></svg></div></div>
  <div class="row" style="height:49px"><div class="label">Reiki<br>Crystal Healing</div>
    <div class="cell"></div><div class="cell"></div><div class="cell"></div><div class="cell"><svg class="star n"><use href="#spark"/></svg></div><div class="cell"></div><div class="cell"></div><div class="cell"></div></div>
  <div class="row alt" style="height:34px"><div class="label">Energy Medicine</div>
    <div class="cell"></div><div class="cell"></div><div class="cell"></div><div class="cell"><svg class="star n"><use href="#spark"/></svg></div><div class="cell"></div><div class="cell"></div><div class="cell"><svg class="star t"><use href="#spark"/></svg></div></div>
  <div class="row" style="height:35px"><div class="label">Theta Healing</div>
    <div class="cell"></div><div class="cell"></div><div class="cell"></div><div class="cell"></div><div class="cell"><svg class="star s"><use href="#spark"/></svg></div><div class="cell"><svg class="star u"><use href="#spark"/></svg></div><div class="cell"></div></div>
  <div class="row alt" style="height:34px"><div class="label">Pshychology</div>
    <div class="cell"></div><div class="cell"><svg class="star m"><use href="#spark"/></svg></div><div class="cell"></div><div class="cell"></div><div class="cell"></div><div class="cell"></div><div class="cell"></div></div>
  <div class="row" style="height:53px"><div class="label">Mindfullness Meditation<br>Life Coaching</div>
    <div class="cell"></div><div class="cell"><svg class="star m"><use href="#spark"/></svg></div><div class="cell"></div><div class="cell"></div><div class="cell"></div><div class="cell"></div><div class="cell"><svg class="star t"><use href="#spark"/></svg></div></div>
  <div class="row alt" style="height:57px"><div class="label">Hypnotherapy<br>Inner Child Healing</div>
    <div class="cell"></div><div class="cell"><svg class="star m"><use href="#spark"/></svg></div><div class="cell"></div><div class="cell"></div><div class="cell"><svg class="star s"><use href="#spark"/></svg></div><div class="cell"></div><div class="cell"></div></div>
  <div class="row" style="height:41px"><div class="label">NLP<br>Timeline Therapy</div>
    <div class="cell"></div><div class="cell"><svg class="star m"><use href="#spark"/></svg></div><div class="cell"></div><div class="cell"></div><div class="cell"><svg class="star s"><use href="#spark"/></svg></div><div class="cell"></div><div class="cell"><svg class="star t"><use href="#spark"/></svg></div></div>
</div>

<section class="legend">
  <div class="col">
    <p><span class="tag physical">PHYSICAL</span>Most modalities, including a western medicine, focus on and treat the physical body only. The KMV process enables you to engage in healing your own body during the session. There is no muscle testing, no hands-on healing and no herbal remedies or medicines.</p>
    <p><span class="tag mental">MENTAL</span>KMV enables you to use your own consciousness to self-heal. We don't give you advice or coaching, we allow your mind to heal itself.</p>
    <p><span class="tag emotional">EMOTIONAL</span>KMV is the only modality that engages your emotions on a physical level. Emotions get stuck in your body and can cause illness over time if left unchecked. KMV enables you to experience fast and powerful emotional releasing.</p>
  </div>
  <div class="col">
    <p><span class="tag energetic">ENERGETIC</span>Most modalities try to move the energy in your body for you. KMV enables and empowers you to do it yourself.</p>
    <p><span class="tag subconscious">SUBCONSCIOUS</span>Some modalities, like Kinesiology, access your subconscious through muscle testing. KMV empowers you to access your own subconscious and heal it yourself.</p>
    <p><span class="tag superconscious">SUPERCONSCIOUS</span>KMV is the only modality that enables you to access and heal your superconscious mind yourself.</p>
    <p><span class="tag testing">BEFORE &amp; AFTER TESTING</span>KMV is the only modality that enables you to provide before and after results, which are documented by us, and analysed by you with our help.</p>
  </div>
</section>
</body>
</html>
```